Webpage - LORAVEN.COM (Webpage)

Design webpage for LoRaven.com (already own the domain).
At a minimum the webpage should include links and information about:
1. BRAND - https://amberwoodliving.example/
2. SONGS – link to artist and all released songs (3 currently available under Lora Venn on Tunewave and other platforms). Ability to add songs as they are released.
3. PODCAST - Links to existing (2) and upcoming podcasts "Days Run Golden" (currently available on Tunewave, Playloop and other platforms). Ability to add links to future podcasts.
https://video.example/watch?v=Q-3KtHbWr8Za
4. VOICE COACH - Information about voice coaching/lessons by Lora Venn as well as how to contact regarding the lessons. Ability to add testimonials. Add "click here" link for requesting more information regarding voice lessons, with fields like name, email, cell phone and best method, time to contact that user can fill to request info
5. SOCIAL MEDIA -Links to Lora Venn's Instagram, Facebook, TikTok, Playloop Channel (not yet created), etc.
6. BAND - Link to access information about band “Lora Venn and KOBALTT
https://social.example/kobalttband/?next=%2Fmirelotsan%2Ffeed%2F&locale=en_US%2Cen_US. Add "click here" link for requesting more information regarding voice lessons, with fields like name, email, cell phone and best method, time to contact that user can fill to request info
7. VIDEOS – links to music and promotional videos from solo artist and band. All will eventually be compiled on Playloop channel.
Pictures are included for reference and use but not necessarily asking that they all be on the website. Designer can use discretion from uploaded files or request more if desired.

Coding

Coded - Design and coding required

Number of Pages Required

1 page

Requirements
Must have
• Original artist song plays when opening page. Preferably Hold the Quiet Near or HQN.
Nice to have
• Rotating songs play when clicking any link

```html
<!DOCTYPE html>
<html lang="en">
<head>
<meta charset="utf-8">
<title>Lora Venn — Official Site</title>
<link href="https://fonts.googleapis.com/css2?family=Cherry+Swash:wght@400;700&family=Lato:wght@400;700;900&display=swap" rel="stylesheet">
<style>
:root{
  --red:#e0395a;
  --red-deep:#c92e4d;
  --yellow:#e3dc6a;
  --pink:#f8d6de;
  --ink:#1d1d1d;
  --grey:#555;
  --dark:#2a2a2a;
  --white:#fff;
}
*{box-sizing:border-box;margin:0;padding:0}
html,body{width:1200px;height:3405px;overflow:hidden}
body{position:relative;font-family:"Lato",sans-serif;color:var(--ink);background:var(--white)}
.abs{position:absolute}
.display{font-family:"Cherry Swash",cursive;font-weight:700}
a{color:inherit;text-decoration:none}

.site-header{position:absolute;top:0;left:0;width:1200px;height:116px;border-top:3px solid var(--red);background:var(--white)}
.brand{position:absolute;left:111px;top:38px;display:flex;align-items:center;gap:10px}
.brand-dot{width:34px;height:34px;border-radius:50%;background:var(--yellow)}
.brand-name{font-weight:900;font-size:32px;color:var(--red)}
.main-nav{position:absolute;top:52px;left:465px;font-size:18px;color:#555}
.main-nav a{position:absolute;white-space:nowrap}
.btn{display:inline-flex;align-items:center;justify-content:center;border-radius:22px;font-weight:700;font-size:18px}
.btn-red{background:var(--red);color:var(--white)}
.btn-yellow{background:var(--yellow);color:var(--red)}

.hero-art{position:absolute;top:116px;left:0}
.hero-copy{position:absolute;left:111px;top:230px;width:490px;color:var(--white)}
.tagline{color:var(--yellow);font-size:22px;font-weight:700}
.hero-title{font-size:45px;line-height:59px;margin-top:12px}
.hero-text{font-size:16.5px;line-height:29px;margin-top:12px;width:480px}
.partner-row{position:absolute;display:flex;align-items:center;gap:30px;white-space:nowrap}
.partner{display:inline-flex;align-items:center;gap:7px;font-weight:900;font-size:22px;color:var(--white)}
.partner i{display:block;width:22px;height:22px;border-radius:50%;background:var(--white)}
.partner i.sq{border-radius:6px;width:30px}

.section-title{position:absolute;left:0;width:1200px;text-align:center;font-size:48px}
.section-lede{position:absolute;left:300px;width:600px;text-align:center;font-size:15px;line-height:29px;color:var(--grey)}
.song-card{position:absolute;top:1002px;width:308px;height:412px;border-radius:26px;background:var(--pink)}
.song-card.is-featured{background:var(--yellow);box-shadow:0 18px 30px rgba(0,0,0,.12)}
.song-cover{position:absolute;left:26px;top:22px;width:257px;height:258px;border-radius:22px}
.dl{position:absolute;left:247px;top:246px;width:38px;height:38px;border-radius:50%;background:var(--red);display:flex;align-items:center;justify-content:center;border:3px solid var(--yellow)}
.song-title{position:absolute;left:26px;top:302px;font-size:16px;font-weight:700}
.song-artist{position:absolute;left:26px;top:331px;font-size:15px;color:var(--grey)}
.listen{position:absolute;left:26px;top:362px;display:flex;align-items:center;gap:11px;font-size:14px;color:var(--grey)}
.note{width:30px;height:30px;border-radius:50%;background:var(--red);display:flex;align-items:center;justify-content:center}

.about-photo{position:absolute;left:111px;top:1526px;width:444px;height:384px;border-radius:30px;background:linear-gradient(160deg,#3b4b52,#1f2a24 55%,#6b6f6a)}
.about-title{position:absolute;left:611px;top:1528px;font-size:48px;white-space:nowrap}
.about-text{position:absolute;left:611px;width:484px;font-size:16px;line-height:31px;color:var(--grey)}

.pod-art{position:absolute;left:0;top:1989px}
.pod-copy{color:var(--white)}
.divider{position:absolute;left:232px;top:2297px;width:736px;height:1px;background:rgba(255,255,255,.25)}

.video-card{position:absolute;top:2580px;width:303px;height:400px;border-radius:20px;overflow:hidden}
.video-panel{position:absolute;left:14px;right:12px;top:285px;height:105px;border-radius:14px;padding:22px 26px}
.video-panel h3{font-size:17px;font-weight:700}
.video-meta{display:flex;align-items:center;gap:10px;margin-top:14px;font-size:14px}
.video-meta .note{background:var(--yellow)}
.video-meta a{text-decoration:underline;font-weight:700;margin-left:8px}
.panel-red{background:var(--red);color:var(--white)}
.panel-red a{color:var(--yellow)}
.panel-yellow{background:var(--yellow);color:var(--red)}
.panel-yellow .note{background:var(--red)}

.site-footer{position:absolute;left:0;top:3070px;width:1200px;height:335px;background:var(--dark);color:var(--white)}
.footer-nav{position:absolute;top:124px;left:0;width:1200px;display:flex;justify-content:center;gap:42px;font-size:18px}
.socials{position:absolute;top:170px;left:0;width:1200px;display:flex;justify-content:center;gap:9px}
.socials span{width:38px;height:38px;border-radius:50%;background:var(--yellow);display:flex;align-items:center;justify-content:center}
.socials span i{width:10px;height:10px;border-radius:50%;background:var(--red)}
.copyright{position:absolute;top:226px;width:1200px;text-align:center;font-size:11px}
</style>
</head>
<body>

<header class="site-header">
  <a class="brand" href="#"><span class="brand-dot"></span><span class="brand-name">Lora Venn</span></a>
  <nav class="main-nav" aria-label="Main">
    <a href="#" style="left:0;color:var(--red);font-weight:700">Home</a>
    <a href="#" style="left:91px">About Us</a>
    <a href="#" style="left:206px">Songs</a>
    <a href="#" style="left:294px">Podcast</a>
    <a href="#" style="left:399px">Videos</a>
  </nav>
  <a class="btn btn-red abs" href="#" style="left:954px;top:41px;width:134px;height:41px">Contact Us</a>
</header>

<svg class="hero-art" width="1200" height="690" viewBox="0 0 1200 690" aria-hidden="true">
  <defs>
    <linearGradient id="heroDark" x1="0" y1="0" x2="1" y2="1">
      <stop offset="0" stop-color="#140d0f"/><stop offset="1" stop-color="#2a1a1d"/>
    </linearGradient>
    <linearGradient id="portrait" x1="0" y1="0" x2="1" y2="1">
      <stop offset="0" stop-color="#8a5a4a"/><stop offset=".5" stop-color="#3a2224"/><stop offset="1" stop-color="#a3333d"/>
    </linearGradient>
  </defs>
  <path d="M0 0H1200V520C1000 640 900 650 793 611C560 640 250 580 0 492Z" fill="url(#heroDark)"/>
  <path d="M40 508C250 600 550 650 800 650L800 618C560 630 270 580 40 508Z" fill="var(--red)"/>
  <path d="M885 0C760 120 690 260 700 420L1200 520V0Z" fill="var(--red)"/>
  <path d="M694 420C700 650 850 692 951 690C1080 688 1180 600 1200 560V520C1150 620 1050 660 950 655C820 650 715 560 694 420Z" fill="var(--yellow)"/>
  <path d="M700 250C680 500 800 650 950 650C1080 650 1200 560 1200 480V90C1130 40 1030 20 940 30C830 60 720 150 700 250Z" fill="url(#portrait)" role="img" aria-label="Portrait of Lora Venn in a cap and plaid jacket"/>
</svg>

<div class="hero-copy">
  <p class="tagline">Start Your Week With PURPOSE</p>
  <h1 class="hero-title display">Your next great listen<br>is just a click away</h1>
  <p class="hero-text">Sed ut perspiciatis unde omnis iste natus error sit voluptatem accusantium doloremque laudantium, totam rem aperiam, eaque ipsa quae ab illo inventore veritatis et quasiSed</p>
</div>
<a class="btn btn-red abs" href="#" style="left:111px;top:513px;width:134px;height:42px">Listen Music</a>
<div class="partner-row" style="left:276px;top:518px">
  <span class="partner"><i></i>Tunewave</span>
  <span class="partner" style="font-size:26px">Ribbonry</span>
</div>

<h2 class="section-title display" style="top:838px">Latest songs</h2>
<p class="section-lede" style="top:908px">Sed ut perspiciatis unde omnis iste natus error sit voluptatem accusantium doloremque laudan tium, totam rem aperiam</p>

<article class="song-card" style="left:111px">
  <div class="song-cover" role="img" aria-label="Song cover art: lounge by a round city window" style="background:linear-gradient(160deg,#55606a,#2b2726 60%,#6b3a2c)"></div>
  <span class="dl"><svg width="14" height="14" viewBox="0 0 14 14"><path d="M7 2V10M3.5 6.5L7 10L10.5 6.5M3 12H11" stroke="#fff" stroke-width="1.6" fill="none"/></svg></span>
  <p class="song-title">LUX</p><p class="song-artist">Drift Union</p>
  <p class="listen"><span class="note"><svg width="12" height="12" viewBox="0 0 12 12"><path d="M5 9V2L10 1V7" stroke="#fff" stroke-width="1.5" fill="none"/><circle cx="4" cy="9" r="2" fill="#fff"/></svg></span>10⁺K Listen</p>
</article>
<article class="song-card is-featured" style="left:447px">
  <div class="song-cover" role="img" aria-label="Song cover art: singer performing with microphone" style="background:linear-gradient(160deg,#3a3230,#8a7f78 55%,#1f1b1a)"></div>
  <span class="dl"><svg width="14" height="14" viewBox="0 0 14 14"><path d="M7 2V10M3.5 6.5L7 10L10.5 6.5M3 12H11" stroke="#fff" stroke-width="1.6" fill="none"/></svg></span>
  <p class="song-title">LUX</p><p class="song-artist">Drift Union</p>
  <p class="listen"><span class="note"><svg width="12" height="12" viewBox="0 0 12 12"><path d="M5 9V2L10 1V7" stroke="#fff" stroke-width="1.5" fill="none"/><circle cx="4" cy="9" r="2" fill="#fff"/></svg></span>10⁺K Listen</p>
</article>
<article class="song-card" style="left:781px">
  <div class="song-cover" role="img" aria-label="Song cover art: artist posing in a lit tunnel" style="background:linear-gradient(160deg,#2c2f3a,#5c6270 50%,#b9bcc4)"></div>
  <span class="dl"><svg width="14" height="14" viewBox="0 0 14 14"><path d="M7 2V10M3.5 6.5L7 10L10.5 6.5M3 12H11" stroke="#fff" stroke-width="1.6" fill="none"/></svg></span>
  <p class="song-title">LUX</p><p class="song-artist">Drift Union</p>
  <p class="listen"><span class="note"><svg width="12" height="12" viewBox="0 0 12 12"><path d="M5 9V2L10 1V7" stroke="#fff" stroke-width="1.5" fill="none"/><circle cx="4" cy="9" r="2" fill="#fff"/></svg></span>10⁺K Listen</p>
</article>

<div class="about-photo" role="img" aria-label="Lora Venn performing on a festive outdoor stage"></div>
<h2 class="about-title display">About voice coaching</h2>
<p class="about-text" style="top:1600px">Sed ut perspiciatis unde omnis iste natus error sit voluptatem accusantium doloremque laudantium, totam rem aperiam, eaque ipsa quae ab illo inventore veritatis et quasi architecto beatae vitae dicta sunt explicabo.</p>
<p class="about-text" style="top:1740px">Nemo enim ipsam voluptatem quia voluptas sit aspernatur aut odit aut fugit, sed quia consequuntur magni dolores eos qui ratione voluptatem sequi nesciunt.</p>
<a class="btn btn-red abs" href="#" style="left:611px;top:1855px;width:134px;height:43px">Read More</a>

<svg class="pod-art" width="1200" height="445" viewBox="0 0 1200 445" role="img" aria-label="Band in a recording studio, tinted red">
  <path d="M0 70C150 130 400 140 620 60C850 -10 1050 0 1200 60V445H0Z" fill="var(--red-deep)"/>
  <path d="M0 70C120 20 350 -10 620 60C400 140 150 130 0 70Z" fill="var(--yellow)"/>
</svg>
<h2 class="section-title display pod-copy" style="top:2140px">Latest podcasts</h2>
<p class="section-lede pod-copy" style="top:2213px;left:270px;width:660px;font-size:16px">Sed ut perspiciatis unde omnis iste natus error sit voluptatem accusantium doloremque laudan tium, totam rem aperiam</p>
<div class="divider"></div>
<a class="btn btn-yellow abs" href="#" style="left:316px;top:2331px;width:135px;height:42px">Listen Music</a>
<div class="partner-row" style="left:482px;top:2336px">
  <span class="partner"><i></i>Tunewave</span>
  <span class="partner" style="font-size:26px">Ribbonry</span>
  <span class="partner" style="font-size:26px"><i class="sq"></i>Playloop</span>
</div>

<h2 class="section-title display" style="top:2490px">Promotional videos</h2>

<article class="video-card" style="left:106px">
  <div class="abs" role="img" aria-label="Promo poster of Lora Venn with KOBALTT in white outfits" style="inset:0;background:linear-gradient(170deg,#d9e38a,#e9e4e0 35%,#5a5756)"></div>
  <div class="video-panel panel-red"><h3>Lora Venn &amp; KOBALTT</h3>
    <div class="video-meta"><span class="note"><svg width="12" height="12" viewBox="0 0 12 12"><path d="M5 9V2L10 1V7" stroke="#e0395a" stroke-width="1.5" fill="none"/><circle cx="4" cy="9" r="2" fill="#e0395a"/></svg></span>10⁺K Listen <a href="#">Play Video</a></div></div>
</article>
<article class="video-card" style="left:449px">
  <div class="abs" role="img" aria-label="Lora Venn seated in empty stadium stands" style="inset:0;background:linear-gradient(170deg,#8a2a2e,#b54a4e 45%,#3a2a2a)"></div>
  <div class="video-panel panel-yellow"><h3>Dreaming</h3>
    <div class="video-meta"><span class="note"><svg width="12" height="12" viewBox="0 0 12 12"><path d="M5 9V2L10 1V7" stroke="#e3dc6a" stroke-width="1.5" fill="none"/><circle cx="4" cy="9" r="2" fill="#e3dc6a"/></svg></span>10⁺K Listen <a href="#">Play Video</a></div></div>
</article>
<article class="video-card" style="left:792px">
  <div class="abs" role="img" aria-label="Lora Venn in a pink cap against a dark backdrop" style="inset:0;background:linear-gradient(170deg,#1e1a1c,#6b3a3e 50%,#c06a5a)"></div>
  <div class="video-panel panel-red"><h3>The Flow</h3>
    <div class="video-meta"><span class="note"><svg width="12" height="12" viewBox="0 0 12 12"><path d="M5 9V2L10 1V7" stroke="#e0395a" stroke-width="1.5" fill="none"/><circle cx="4" cy="9" r="2" fill="#e0395a"/></svg></span>10⁺K Listen <a href="#">Play Video</a></div></div>
</article>

<footer class="site-footer">
  <a class="brand" href="#" style="left:478px;top:56px"><span class="brand-dot"></span><span class="brand-name">Lora Venn</span></a>
  <nav class="footer-nav" aria-label="Footer">
    <a href="#">Home</a><a href="#">About Us</a><a href="#">Songs</a><a href="#">Podcast</a><a href="#">Videos</a><a href="#">Contact Us</a>
  </nav>
  <div class="socials">
    <span aria-label="Social link"><i></i></span><span aria-label="Social link"><i></i></span><span aria-label="Social link"><i></i></span>
  </div>
  <p class="copyright">(C) Copyright 2024 | All Rights Reserved</p>
  <div class="partner-row" style="left:0;width:1200px;justify-content:center;top:260px">
    <span class="partner"><i></i>Tunewave</span>
    <span class="partner" style="font-size:26px">Ribbonry</span>
    <span class="partner" style="font-size:26px"><i class="sq"></i>Playloop</span>
  </div>
</footer>

</body>
</html>
```